Flyer to advertise gutter cleaning throughout the Autumn and winter monthss

I need a new flyer to advertise gutter and driveway cleaning, roof and gutter repairs.

I am an experienced licensed Plumber and Gasfitter looking to broaden my scope of work to gutter cleaning. I am experienced in cleaning gutter and live in a area with large gum trees. I wont something that's clear, eye catching but not too busy.

Flyer requirements: Free roof inspection - no obligation. Gutter Cleaning from $199. Pictures of men using blower or hands to clean roof gutters (no obvious faces) to be included. Australian looking houses.

A mention that 'All general plumbing maintenance' is offered as other services but not too much wording about this as the target is for gutter cleaning.

Phone number: 0427 385 912 (in this format)
Business Name: Larkvale Plumbing & Gasfitting
License: 3175420
ABN: 71364058227
Web: http://larkvaleplumbing.example.site/

Target Market(s)

Elderly - busy working class

Industry/Entity Type

Plumber

Font styles to use
Sans Serif

Colors
0355a3
fbed22
ec1f27
f78f20

Requirements
Must have
• Roof Gutter Cleaning pictures
• Men in protective clothing if possible
Nice to have
• More information:
• Prevent against flooding, mold, rust, rotting and corrosion now!
• Gutter Cleaning Services
• • Remove leaves, sticks, and other debris
• • Clear away clogs
• • Test your downpipes
• • Pinpoint any gutter issues
• • Repair gutter
• With regular service, you can count on your property to be well-protected no matter what the forecast!
Should not have
• Houses that don't look Australian

```html
<!DOCTYPE html>
<html lang="en">
<head>
<meta charset="utf-8">
<title>Larkvale Plumbing &amp; Gasfitting – Gutter Cleaning Flyer</title>
<link rel="stylesheet" href="https://fonts.googleapis.com/css2?family=Open+Sans:wght@400;600;700&family=Oswald:wght@600;700&display=swap">
<style>
:root{
  --blue:#0355a3;
  --navy:#0b2a63;
  --yellow:#f2cb0c;
  --yellow-deep:#d9b700;
  --red:#ec1f27;
  --white:#ffffff;
  --ink:#1c1c1c;
  --grey:#e9eaec;
}
*{margin:0;padding:0;box-sizing:border-box}
html,body{width:973px;height:1200px;overflow:hidden;background:#fff}
body{font-family:"Open Sans",Arial,sans-serif;position:relative}
.flyer{position:absolute;inset:0;overflow:hidden}

.hero-photo{position:absolute;left:0;top:0;width:973px;height:432px;
  background:linear-gradient(180deg,#8fb6de 0%,#dfe6ee 28%,#e9ecef 55%,#9aa39a 72%,#4f7a2e 88%,#5d8c35 100%)}
.brand-swoosh{position:absolute;left:0;top:0;width:973px;height:432px}
.brand{position:absolute;left:682px;top:44px;display:flex;align-items:center;gap:12px}
.brand-mark{width:58px;height:58px;border-radius:50%;background:var(--blue);flex:none}
.brand-name{font-weight:700;font-size:17px;line-height:1.15;color:var(--ink);letter-spacing:-.2px}

.headline{position:absolute;left:0;top:432px;width:973px;height:127px;
  background:linear-gradient(90deg,var(--blue) 0%,#0a3f88 55%,var(--navy) 100%);
  display:flex;align-items:center;justify-content:center;text-align:center;
  color:var(--white);font-weight:700;font-size:30px;line-height:1.32;letter-spacing:-.3px}

.offers{position:absolute;left:0;top:559px;width:973px;height:541px;
  background:radial-gradient(ellipse at 50% 40%,#f7f7f8 0%,var(--grey) 70%,#dcdde0 100%)}

.offer{position:absolute;border-radius:50%}
.offer-ring{width:262px;height:262px;border:2px solid #b9bcc0;background:rgba(255,255,255,.4)}
.offer-photo{position:absolute;left:12px;top:12px;width:234px;height:234px;border-radius:50%;overflow:hidden;
  display:flex;flex-direction:column;align-items:center;justify-content:center;text-align:center}
.offer-photo.gutter{background:radial-gradient(circle at 40% 35%,#7c8f6a 0%,#5d6a58 50%,#3e4744 100%)}
.offer-photo.driveway{background:radial-gradient(circle at 60% 40%,#9a9ea3 0%,#6c7176 55%,#3f4449 100%)}
.offer-label{color:var(--white);font-weight:700;font-size:23px;line-height:1.3;text-shadow:0 1px 3px rgba(0,0,0,.45)}
.offer-price{font-family:"Oswald",Impact,sans-serif;font-weight:700;font-size:50px;line-height:1.05;color:var(--yellow);text-shadow:0 2px 3px rgba(0,0,0,.4)}
.offer-left{left:90px;top:581px}
.offer-right{left:613px;top:581px}

.offer-center{left:352px;top:573px;width:284px;height:284px;background:radial-gradient(circle at 50% 40%,#ead22a 0%,var(--yellow-deep) 100%);
  box-shadow:0 10px 18px rgba(0,0,0,.18)}
.offer-center::before{content:"";position:absolute;inset:10px;border-radius:50%;border:2px solid rgba(255,255,255,.7)}
.offer-center .inner{position:absolute;inset:0;display:flex;flex-direction:column;align-items:center;justify-content:center;text-align:center;color:var(--white)}
.free-title{font-family:"Oswald",Impact,sans-serif;font-weight:700;font-size:37px;line-height:1.12;text-transform:uppercase}
.free-sub{font-weight:700;font-size:23px;margin-top:4px}
.divider{width:174px;height:2px;background:var(--white);margin:14px 0 12px}
.reg{font-size:15px;line-height:1.35}

.services{position:absolute;left:42px;top:910px;width:885px;height:164px;border:2px dotted var(--red);border-radius:8px}
.services-tag{position:absolute;left:287px;top:891px;width:378px;height:40px;background:var(--red);border-radius:8px;
  color:var(--white);font-weight:600;font-size:20px;display:flex;align-items:center;justify-content:center}
.service-list{position:absolute;list-style:none;font-size:20.5px;color:var(--ink)}
.service-list li{height:36px;display:flex;align-items:center;gap:10px}
.service-list svg{flex:none}
.col-a{left:62px;top:942px}
.col-b{left:504px;top:942px}

.footer{position:absolute;left:0;top:1100px;width:973px;height:100px}
.footer svg{position:absolute;inset:0}
.contact{position:absolute;left:43px;top:1110px;color:var(--white)}
.contact-cta{font-weight:600;font-size:23px;letter-spacing:-.2px}
.contact-phone{display:flex;align-items:center;gap:14px;margin-top:6px;font-weight:700;font-size:40px;letter-spacing:.5px;line-height:1}
.web{position:absolute;left:600px;top:1154px;width:362px;text-align:center;color:var(--white);font-weight:600;font-size:23px}
</style>
</head>
<body>
<main class="flyer">

  <div class="hero-photo" role="img" aria-label="Photo of a worker's arms holding a pressure washer wand in front of a white weatherboard two-storey house with garden and lawn"></div>
  <svg class="brand-swoosh" viewBox="0 0 973 432" aria-hidden="true">
    <path d="M548,0 C612,140 790,202 973,206 L973,196 C790,192 624,128 562,0 Z" fill="var(--yellow)"/>
    <path d="M549,0 C618,128 790,182 973,184 L973,198 C790,196 612,136 538,0 Z" fill="var(--navy)"/>
    <path d="M562,0 C628,120 790,174 973,178 L973,0 Z" fill="var(--white)"/>
  </svg>
  <div class="brand">
    <span class="brand-mark"></span>
    <p class="brand-name">LARKVALE PLUMBING<br>&amp; GASFITTING</p>
  </div>

  <h1 class="headline">PREVENT AGAINST FLOODING, MOLD, RUST,<br>ROTTING AND CORROSION NOW!</h1>

  <section class="offers" role="img" aria-label="Light grey background with water droplets"></section>

  <div class="offer offer-ring offer-left">
    <div class="offer-photo gutter" role="img" aria-label="Close-up of a roof gutter being cleaned with a blower">
      <p class="offer-label">GUTTER<br>CLEANING FROM</p>
      <p class="offer-price">$199</p>
    </div>
  </div>

  <div class="offer offer-center">
    <div class="inner">
      <p class="free-title">Free Roof<br>Inspection</p>
      <p class="free-sub">NO OBLIGATION</p>
      <span class="divider"></span>
      <p class="reg">License: 3175420<br>ABN: 71364058227</p>
    </div>
  </div>

  <div class="offer offer-ring offer-right">
    <div class="offer-photo driveway" role="img" aria-label="Pressure washer nozzle cleaning a concrete driveway">
      <p class="offer-label">DRIVEWAY<br>CLEANING FROM</p>
      <p class="offer-price">$299</p>
    </div>
  </div>

  <div class="services"></div>
  <h2 class="services-tag">GUTTER CLEANING SERVICES</h2>
  <ul class="service-list col-a">
    <li><svg width="14" height="14" viewBox="0 0 14 14"><circle cx="7" cy="7" r="7" fill="var(--red)"/><path d="M5.5 4 8.5 7 5.5 10" stroke="#fff" stroke-width="1.8" fill="none"/></svg>Remove leaves, sticks, and other debris</li>
    <li><svg width="14" height="14" viewBox="0 0 14 14"><circle cx="7" cy="7" r="7" fill="var(--red)"/><path d="M5.5 4 8.5 7 5.5 10" stroke="#fff" stroke-width="1.8" fill="none"/></svg>Clear away clogs</li>
    <li><svg width="14" height="14" viewBox="0 0 14 14"><circle cx="7" cy="7" r="7" fill="var(--red)"/><path d="M5.5 4 8.5 7 5.5 10" stroke="#fff" stroke-width="1.8" fill="none"/></svg>Test your downpipes</li>
  </ul>
  <ul class="service-list col-b">
    <li><svg width="14" height="14" viewBox="0 0 14 14"><circle cx="7" cy="7" r="7" fill="var(--red)"/><path d="M5.5 4 8.5 7 5.5 10" stroke="#fff" stroke-width="1.8" fill="none"/></svg>Pinpoint any gutter issues</li>
    <li><svg width="14" height="14" viewBox="0 0 14 14"><circle cx="7" cy="7" r="7" fill="var(--red)"/><path d="M5.5 4 8.5 7 5.5 10" stroke="#fff" stroke-width="1.8" fill="none"/></svg>Repair Gutters</li>
    <li><svg width="14" height="14" viewBox="0 0 14 14"><circle cx="7" cy="7" r="7" fill="var(--red)"/><path d="M5.5 4 8.5 7 5.5 10" stroke="#fff" stroke-width="1.8" fill="none"/></svg>Your property will be well-protected</li>
  </ul>

  <footer class="footer">
    <svg viewBox="0 0 973 100" aria-hidden="true">
      <defs>
        <linearGradient id="footBlue" x1="0" x2="1">
          <stop offset="0" stop-color="#0a3f88"/>
          <stop offset="1" stop-color="var(--blue)"/>
        </linearGradient>
      </defs>
      <rect width="973" height="100" fill="var(--yellow)"/>
      <path d="M0,0 H610 L584,100 H0 Z" fill="var(--white)"/>
      <path d="M0,0 H598 L572,100 H0 Z" fill="url(#footBlue)"/>
    </svg>
  </footer>
  <div class="contact">
    <p class="contact-cta">CONTACT US TODAY!!!</p>
    <p class="contact-phone">
      <svg width="38" height="38" viewBox="0 0 38 38" aria-hidden="true"><circle cx="19" cy="19" r="17" fill="none" stroke="#fff" stroke-width="2.5"/><path d="M13 10.5c1-.8 2-.6 2.6.3l1.8 2.8c.5.8.3 1.7-.4 2.2l-1.3 1c.9 2.3 2.7 4.2 5 5.2l1-1.3c.5-.7 1.5-.9 2.2-.4l2.8 1.8c.9.6 1.1 1.7.3 2.6l-1.5 1.7c-.8.9-2.2 1.2-3.5.7-5-1.9-8.9-5.8-10.8-10.8-.5-1.3-.2-2.7.7-3.5z" fill="#fff"/></svg>
      0427 385 912
    </p>
  </div>
  <p class="web">larkvaleplumbing.example.site</p>

</main>
</body>
</html>
```